Vantro cards

I am in the auto motive, transportation business I would like a business card that is Something cool, modern edgy, having to do with car culture. I offer towing service for high and exotic cars. I also provide towing for collisions and car accidents. I offer open and enclosed transport nationwide.

Target Market(s)

Car culture people high end auto collectors

Industry/Entity Type

Towing car carrier

Contact Information for Business Card

My company colors black yellow and silver

Font styles to use
Serif

```html
<!DOCTYPE html>
<html lang="en">
<head>
<meta charset="utf-8">
<title>Vantro Transportation – Business Card</title>
<link rel="stylesheet" href="https://fonts.googleapis.com/css2?family=Montserrat:ital,wght@0,400;0,500;0,600;0,800;1,400;1,800&display=swap">
<style>
  :root {
    --ink: #050505;
    --yellow: #f5c400;
    --paper: #dedede;
    --white: #f4f4f4;
    --backdrop: #e6e6e6;
  }
  * { box-sizing: border-box; margin: 0; padding: 0; }
  html, body { width: 1200px; height: 900px; overflow: hidden; }
  body {
    background: var(--backdrop);
    font-family: "Montserrat", sans-serif;
    display: flex; flex-direction: column; align-items: center; justify-content: center; gap: 40px;
  }
  .card { position: relative; width: 700px; height: 400px; overflow: hidden; box-shadow: 0 6px 18px rgba(0,0,0,.18); }

  /* Front */
  .card-front { background: var(--paper); }
  .card-front .shape { position: absolute; inset: 0; }
  .brand {
    position: absolute; left: 55px; top: 0; width: 240px; height: 400px;
    display: flex; flex-direction: column; align-items: center; justify-content: center; gap: 10px;
    color: var(--ink); font-weight: 800; text-transform: uppercase; text-align: center;
  }
  .brand-mark { width: 26px; height: 26px; background: var(--yellow); }
  .brand-name { font-size: 46px; letter-spacing: 1px; line-height: 1; }
  .brand-sub { font-size: 15px; letter-spacing: 1px; }

  .person { position: absolute; left: 394px; top: 64px; color: var(--white); }
  .person-name { font-size: 28px; font-weight: 800; font-style: italic; letter-spacing: -0.5px; }
  .person-title { font-size: 16px; font-style: italic; letter-spacing: 1px; margin-top: 2px; }
  .divider { position: absolute; left: 394px; top: 133px; width: 250px; height: 3px; background: var(--white); }
  .divider::before { content: ""; position: absolute; left: 0; top: -1px; width: 60px; height: 5px; background: var(--yellow); }

  .contact { position: absolute; left: 350px; display: flex; align-items: center; color: var(--white); }
  .contact svg { width: 34px; height: 34px; fill: var(--yellow); }
  .contact .bar { width: 1px; height: 34px; background: var(--white); margin: 0 20px 0 16px; }
  .contact p { font-size: 16px; line-height: 1.3; }
  .contact-phone { top: 170px; } .contact-phone p { font-weight: 600; }
  .contact-web { top: 236px; }
  .contact-place { top: 300px; }

  /* Back */
  .card-back { background: var(--ink); color: var(--white); display: flex; flex-direction: column; align-items: center; justify-content: center; }
  .stripes { position: absolute; left: 0; right: 0; height: 5px;
    background: repeating-linear-gradient(90deg, var(--yellow) 0 26px, transparent 26px 60px); }
  .stripes-top { top: 0; } .stripes-bottom { bottom: 0; }
  .back-brand { display: flex; align-items: center; gap: 12px; color: var(--yellow); font-weight: 800; font-size: 40px; text-transform: uppercase; letter-spacing: 1px; }
  .back-brand .brand-mark { width: 24px; height: 24px; border-radius: 50%; background: var(--yellow); }
  .helpline-label { color: var(--yellow); font-size: 18px; font-style: italic; margin-top: 22px; }
  .helpline-number { font-size: 30px; font-weight: 800; letter-spacing: 2px; }
</style>
</head>
<body>

<section class="card card-front">
  <svg class="shape" viewBox="0 0 700 400" aria-hidden="true">
    <path d="M424 0 Q255 140 322 400 L345 400 Q285 150 450 0 Z" fill="var(--yellow)"/>
    <path d="M450 0 L700 0 L700 400 L345 400 Q285 150 450 0 Z" fill="var(--ink)"/>
  </svg>

  <div class="brand">
    <span class="brand-mark"></span>
    <span class="brand-name">Vantro</span>
    <span class="brand-sub">Transportation</span>
  </div>

  <div class="person">
    <h1 class="person-name">Marek Dalton</h1>
    <p class="person-title">Operation Manager</p>
  </div>
  <div class="divider"></div>

  <div class="contact contact-phone">
    <svg viewBox="0 0 24 24" aria-hidden="true"><path d="M6.6 10.8a15.1 15.1 0 0 0 6.6 6.6l2.2-2.2c.3-.3.7-.4 1-.2 1.1.4 2.3.6 3.6.6.6 0 1 .4 1 1V20c0 .6-.4 1-1 1A17 17 0 0 1 3 4c0-.6.4-1 1-1h3.5c.6 0 1 .4 1 1 0 1.3.2 2.5.6 3.6.1.3 0 .7-.2 1z"/></svg>
    <span class="bar"></span>
    <p>+1-555-014-2290<br>+1-555-014-2290</p>
  </div>

  <div class="contact contact-web">
    <svg viewBox="0 0 24 24" aria-hidden="true"><path d="M2 3l20 9-20 9 4-9zM6 12l-2 6 14-6z"/></svg>
    <span class="bar"></span>
    <p>hello@vantrotow.com<br>www.vantrotransport.com</p>
  </div>

  <div class="contact contact-place">
    <svg viewBox="0 0 24 24" aria-hidden="true"><path d="M12 3 1 12h3v9h6v-6h4v6h6v-9h3z"/></svg>
    <span class="bar"></span>
    <p>4120 Harlow Ave., Texas City,<br>4120 Harlow</p>
  </div>
</section>

<section class="card card-back">
  <div class="stripes stripes-top"></div>
  <div class="back-brand"><span class="brand-mark"></span>Vantro</div>
  <p class="helpline-label">Help Line 24x7</p>
  <p class="helpline-number">800-55017</p>
  <div class="stripes stripes-bottom"></div>
</section>

</body>
</html>
```